Mental Health Clinic Website

website for a mental health clinic. two files describing the website are attached, in case of conflicting info the word document is priority.

Target Market(s)

Ohio / Pennsylvania residents

Industry/Entity Type

Health Care

Coding

Coded - Design and coding required

Number of Pages Required

5+ page

Requirements
Must have
• see attached

```html
<!DOCTYPE html>
<html lang="en">
<head>
<meta charset="utf-8">
<title>Serenova Wellness Center</title>
<link href="https://fonts.googleapis.com/css2?family=Lato:wght@400;700;900&display=swap" rel="stylesheet">
<style>
:root{
  --blue:#1f5fae;
  --blue-dark:#173f80;
  --blue-footer:#1f4f9c;
  --green:#3f9c48;
  --form-green:#5a9e3c;
  --yellow:#f3d21c;
  --red:#e3202a;
  --ink:#222;
  --text:#4a4a4a;
  --line:#c9c9c9;
  --pale:#eef1f6;
}
*{box-sizing:border-box;margin:0;padding:0}
html,body{width:1200px;height:4478px;overflow:hidden}
body{position:relative;font-family:'Lato',sans-serif;color:var(--text);background:#fff}
.abs{position:absolute}

/* hero */
.hero{left:0;top:0;width:1200px;height:720px;background:linear-gradient(180deg,#6aa6d8 0%,#a9cbe6 35%,#c9dcb0 55%,#8fbf4a 75%,#5d9a2f 100%)}
.hero-wave{left:0;top:600px;width:1200px;height:140px}
.dots{left:570px;top:636px;display:flex;gap:12px}
.dots span{width:14px;height:14px;border-radius:50%;border:2px solid #fff}
.dots span.on{background:#fff}

.brand-panel{left:105px;top:0;width:262px;height:500px}
.brand-top{height:255px;background:#fff;display:flex;flex-direction:column;align-items:center;justify-content:flex-end;padding-bottom:26px}
.brand-mark{width:92px;height:92px;border-radius:50%;background:var(--blue);margin-bottom:22px}
.brand-name{font-weight:900;color:var(--ink);font-size:17px;text-align:center;line-height:1.3;text-transform:uppercase}
.main-nav{position:absolute;left:0;top:255px;width:262px;height:240px}
.main-nav svg{position:absolute;left:0;top:0}
.main-nav ul{position:relative;list-style:none;padding-top:30px}
.main-nav li{width:190px;margin:0 auto;text-align:center;color:#fff;font-size:18px;padding:7px 0;border-bottom:1px solid rgba(255,255,255,.35)}
.main-nav li:last-child{border-bottom:none}

/* welcome */
.welcome-title{left:0;top:756px;width:1200px;text-align:center;font-weight:900;font-size:32px;line-height:1.25;color:var(--ink);text-transform:uppercase}
.welcome-title span{display:block;color:var(--blue)}
.welcome-art{left:118px;top:866px;width:266px;height:390px;border-radius:120px 120px 20px 20px;background:radial-gradient(circle at 50% 35%,#f2a83a 0%,#d84a3a 30%,#4c9a4a 55%,#2f7fd0 75%,#fff 76%)}
.welcome-text{left:418px;top:878px;width:660px;font-size:16.5px;line-height:1.45}
.welcome-text p{margin-bottom:22px}

/* about */
.about-bg{left:0;top:1240px;width:1200px;height:1110px}
.about-title{left:138px;top:1470px;color:#fff;font-weight:900;font-size:32px;text-transform:uppercase}
.about-text{left:136px;top:1532px;width:500px;color:#fff;font-weight:700;font-size:16.5px;line-height:1.45}
.about-text p{margin-bottom:18px}
.langs{display:grid;grid-template-columns:104px 100px;row-gap:6px;font-size:15px}
.about-photo{left:642px;top:1432px;width:420px;height:420px;border-radius:50%;border:8px solid #fff;background:linear-gradient(180deg,#f4f4f4,#d9d5cf 70%,#c8c2ba)}

.team{left:100px;top:1924px;width:1030px;display:flex;justify-content:space-between}
.member{width:196px;text-align:center;color:#fff}
.member-photo{width:146px;height:146px;margin:0 auto 12px;border-radius:50%;border:4px solid #fff;background:linear-gradient(180deg,#dde3ea,#9fb0c2)}
.member h3{font-size:19px;font-weight:900}
.member .role{font-size:14px;margin:2px 0 6px}
.member p.bio{font-size:13px;line-height:1.3;opacity:.9;height:70px}
.member .btn{display:inline-block;margin-top:12px;border:2px solid #fff;padding:6px 12px;font-size:11.5px;font-weight:700}

/* services */
.services-title{left:0;top:2384px;width:1200px;text-align:center;font-weight:900;font-size:32px;color:var(--ink);text-transform:uppercase}
.tabs{left:110px;top:2466px;width:974px;height:192px;display:flex;border:2px solid #d4d4d4}
.tab{flex:1;border-left:2px solid #d4d4d4;display:flex;flex-direction:column;align-items:center;justify-content:center;text-align:center;color:var(--blue);font-weight:700;font-size:14px;text-transform:uppercase;line-height:1.25;padding:0 14px;position:relative}
.tab:first-child{border-left:none}
.tab svg{margin-bottom:12px}
.tab.active{background:var(--red);color:#fff}
.tab.active::after{content:"";position:absolute;left:50%;bottom:-22px;margin-left:-22px;border:22px solid transparent;border-bottom:none;border-top-color:var(--red)}
.service-photo{left:113px;top:2782px;width:435px;height:302px;background:linear-gradient(135deg,#e9eef3,#b9c6d2 55%,#8da2b4)}
.service-card{left:561px;top:2746px;width:526px;height:394px;border:2px solid var(--blue);background:#fff;padding:46px 50px 0 100px}
.service-card h2{color:var(--blue);font-size:27px;font-weight:700;text-transform:uppercase;margin-bottom:20px}
.service-card p{font-size:16px;line-height:1.45;margin-bottom:20px}

/* reads */
.reads-bg{left:0;top:3100px;width:1200px;height:640px}
.reads-title{left:0;top:3302px;width:1200px;text-align:center;font-weight:900;font-size:32px;color:var(--ink);text-transform:uppercase}
.book{top:3373px;width:478px;height:239px;background:#fff;box-shadow:0 2px 8px rgba(0,0,0,.08);display:flex;padding:26px 22px}
.book-cover{width:200px;height:174px;flex:none}
.book-info{padding-left:22px}
.book h3{color:var(--blue);font-size:21px;font-weight:700}
.book .author{color:var(--form-green);font-size:15px;font-weight:700;margin:4px 0 10px}
.book p{font-size:13px;line-height:1.4}

/* contact */
.map{left:0;top:3740px;width:1200px;height:500px;background:linear-gradient(160deg,#ecebe7,#e3e2dd 60%,#ddd)}
.contact-card{left:137px;top:3895px;width:332px;height:240px;background:#fff;box-shadow:0 2px 10px rgba(0,0,0,.2);padding:36px 52px}
.contact-card h2{color:var(--blue);font-size:27px;font-weight:900;text-transform:uppercase;margin-bottom:16px}
.contact-card p{color:var(--blue);font-weight:700;font-size:15.5px;line-height:1.55}
.form{left:746px;top:3821px;width:360px;height:398px;background:var(--form-green);padding:22px 30px}
.form h2{color:#fff;font-size:29px;font-weight:700;text-align:center;margin-bottom:16px}
.field{height:38px;background:#fff;margin-bottom:14px;padding:10px 12px;font-size:13px;color:#777}
.check{display:flex;gap:8px;color:#fff;font-weight:700;font-size:13px;line-height:1.25;margin:4px 0 12px}
.check span.box{width:14px;height:14px;background:#fff;flex:none;margin-top:1px}
.submit{height:48px;background:#1b1b1b;color:#fff;font-weight:900;font-size:20px;text-align:center;line-height:48px;text-transform:uppercase}

/* footer */
.footer{left:0;top:4239px;width:1200px;height:173px;background:var(--blue-footer);display:flex;align-items:center;justify-content:center;gap:70px;color:#fff;font-weight:700;font-size:17px}
.footer div{display:flex;align-items:center;gap:10px}
.copyright{left:0;top:4412px;width:1200px;height:66px;background:var(--blue-dark);color:#fff;font-size:13px;text-align:center;line-height:66px}
</style>
</head>
<body>

<div class="abs hero" role="img" aria-label="Photo of a person with raised arms standing in a green meadow under a blue sky"></div>
<svg class="abs hero-wave" viewBox="0 0 1200 140" aria-hidden="true">
  <path d="M0 60 C300 120 700 110 1200 20 L1200 140 L0 140 Z" fill="var(--yellow)"/>
  <path d="M0 88 C300 135 700 125 1200 55 L1200 140 L0 140 Z" fill="#fff"/>
</svg>
<div class="abs dots"><span></span><span class="on"></span><span></span></div>

<header class="abs brand-panel">
  <div class="brand-top">
    <div class="brand-mark"></div>
    <div class="brand-name">Serenova<br>Wellness Center</div>
  </div>
  <nav class="main-nav">
    <svg width="262" height="240" viewBox="0 0 262 240" aria-hidden="true"><path d="M0 0 H262 V205 C180 240 90 245 0 220 Z" fill="var(--blue)"/></svg>
    <ul><li>Home</li><li>About Us</li><li>Services</li><li>Good Reads</li><li>Contact</li></ul>
  </nav>
</header>

<h1 class="abs welcome-title"><span>Welcome to</span>Serenova Wellness Center</h1>
<div class="abs welcome-art" role="img" aria-label="Colourful tree illustration held by a hand"></div>
<div class="abs welcome-text">
  <p>Each individual is unique with unique personality and unique needs. Therefore we provide individual treatment customized for you or your child. Multiculturalism also informs our practice. We are a full service mental health practice with the capacity to serve adults, children, teens and their parents.</p>
  <p>We provide high quality evidence based treatment and care including medication management, pharmacogenomic testing, individual psychotherapy, group psychotherapy, art therapy, CBT, DBT and trauma therapy. Our providers are experts in treating variety of illnesses such as depression, anxiety, schizophrenia, ADHD, gender identity concerns and PTSD.</p>
  <p>We are experienced in a variety of methods that help people achieve their psychological goals, and we will discuss with you the best ways to attain the health and wellness that you deserve. We are committed to helping you achieve your optimal level of emotional functioning and fulfill a successful life.</p>
</div>

<svg class="abs about-bg" viewBox="0 0 1200 1110" aria-hidden="true">
  <defs><linearGradient id="aboutGrad" x1="0" y1="0" x2="1" y2="0.4"><stop offset="0" stop-color="#1d55a8"/><stop offset=".55" stop-color="#1f6aa0"/><stop offset="1" stop-color="#3f9c48"/></linearGradient></defs>
  <path d="M0 140 C400 155 900 120 1200 40 L1200 960 C900 1040 400 1060 0 1020 Z" fill="url(#aboutGrad)"/>
  <path d="M560 128 C880 115 1100 60 1200 5 L1200 42 C1000 115 800 135 560 128 Z" fill="var(--yellow)"/>
  <path d="M0 1020 C400 1060 900 1040 1200 960 L1200 990 C900 1085 400 1105 0 1062 Z" fill="var(--yellow)"/>
</svg>
<h2 class="abs about-title">About Us</h2>
<div class="abs about-text">
  <p>You will find a number of highly specialized – experienced and caring therapists and psychiatrists in Serenova Center. We provide medication management and psychotherapy (counseling) across the lifespan.<br>– children, teens and adults.</p>
  <p>Other than English, we speak the following languages</p>
  <div class="langs"><span>Spanish</span><span>Farsi</span><span>German</span><span>Hebrew</span></div>
</div>
<div class="abs about-photo" role="img" aria-label="Photo of a woman meditating in a lotus pose"></div>

<section class="abs team">
  <div class="member"><div class="member-photo" role="img" aria-label="Staff portrait"></div><h3>Person Name</h3><div class="role">Designation</div><p class="bio">Aenean ac turpis egestas. Cras id elit integer quis urna Ut ante enim dapibus malesuada fring</p><span class="btn">Make an appointment</span></div>
  <div class="member"><div class="member-photo" role="img" aria-label="Staff portrait"></div><h3>Person Name</h3><div class="role">Designation</div><p class="bio">Aenean ac turpis egestas. Cras id elit integer quis urna Ut ante enim dapibus malesuada fring</p><span class="btn">Make an appointment</span></div>
  <div class="member"><div class="member-photo" role="img" aria-label="Staff portrait"></div><h3>Person Name</h3><div class="role">Designation</div><p class="bio">Aenean ac turpis egestas. Cras id elit integer quis urna Ut ante enim dapibus malesuada fring</p><span class="btn">Make an appointment</span></div>
  <div class="member"><div class="member-photo" role="img" aria-label="Staff portrait"></div><h3>Person Name</h3><div class="role">Designation</div><p class="bio">Aenean ac turpis egestas. Cras id elit integer quis urna Ut ante enim dapibus malesuada fring</p><span class="btn">Make an appointment</span></div>
  <div class="member"><div class="member-photo" role="img" aria-label="Staff portrait"></div><h3>Person Name</h3><div class="role">Designation</div><p class="bio">Aenean ac turpis egestas. Cras id elit integer quis urna Ut ante enim dapibus malesuada fring</p><span class="btn">Make an appointment</span></div>
</section>

<h2 class="abs services-title">Our Services</h2>
<div class="abs tabs">
  <div class="tab active"><svg width="56" height="60" viewBox="0 0 56 60" fill="none" stroke="#fff" stroke-width="2.5"><rect x="8" y="8" width="40" height="48" rx="3"/><rect x="20" y="3" width="16" height="9" rx="2"/><path d="M28 22v16M20 30h16"/></svg>Medication<br>Management</div>
  <div class="tab"><svg width="60" height="60" viewBox="0 0 60 60" fill="none" stroke="var(--blue)" stroke-width="2.5"><circle cx="22" cy="14" r="8"/><path d="M10 56V34a12 12 0 0 1 24 0v22"/><circle cx="42" cy="22" r="6"/><path d="M34 56V40a8 8 0 0 1 16 0v16"/></svg>Psychotherapy:<br>Individual, Group,<br>Couples, and Family</div>
  <div class="tab"><svg width="64" height="56" viewBox="0 0 64 56" fill="none" stroke="var(--blue)" stroke-width="2.5"><path d="M32 4C14 4 4 16 4 28s10 24 24 24c6 0 6-6 2-9-3-3 0-8 5-8h8c10 0 17-5 17-13C60 12 48 4 32 4Z"/><circle cx="18" cy="22" r="4"/><circle cx="30" cy="14" r="4"/><circle cx="44" cy="18" r="4"/></svg>Art Therapy</div>
  <div class="tab"><svg width="56" height="60" viewBox="0 0 56 60" fill="none" stroke="var(--blue)" stroke-width="2.5"><circle cx="28" cy="22" r="14"/><path d="M12 58c0-10 7-16 16-16s16 6 16 16"/><path d="M4 22h6M46 22h6M28 2v4"/></svg>Treatment<br>Approach</div>
  <div class="tab"><svg width="56" height="60" viewBox="0 0 56 60" fill="none" stroke="var(--blue)" stroke-width="2.5"><circle cx="28" cy="16" r="11"/><path d="M8 58V46c0-8 9-12 20-12s20 4 20 12v12"/><path d="M22 42h12M28 36v12"/></svg>Treatment<br>Areas</div>
</div>
<div class="abs service-photo" role="img" aria-label="Photo of a doctor writing notes beside pills and a laptop"></div>
<article class="abs service-card">
  <h2>Medication Management</h2>
  <p>Pellentesque faucibus Ut accumsan ultricies elit Maecenas at justo id velit placerat molestie Donec dictum lectus non odio Cras a ante vitae enim</p>
  <p>Mauris nunc quam venenatis nec euismod sit amet egestas placerat est Pellentesque habitant morbi tristique senectus et netus et malesuada fames ac turpis egestas Cras id elit integer quis urna Ut ante enim dapibus malesuada fringilla eu condi</p>
</article>

<svg class="abs reads-bg" viewBox="0 0 1200 640" aria-hidden="true">
  <path d="M0 110 C400 110 900 70 1200 0 L1200 640 L0 640 Z" fill="var(--pale)"/>
  <path d="M560 98 C880 90 1100 45 1200 8 L1200 42 C1000 95 800 110 560 98 Z" fill="var(--yellow)"/>
</svg>
<h2 class="abs reads-title">Good Reads</h2>
<article class="abs book" style="left:110px">
  <div class="book-cover" role="img" aria-label="Photo of old books on a shelf" style="background:linear-gradient(90deg,#5a2a1a,#9a6a3a 40%,#3d2a20 70%,#7a4a2a)"></div>
  <div class="book-info"><h3>Book Title here</h3><div class="author">Author Name</div><p>Pellentesque faucibus Ut accumsan ultricies elit Maecenas at justo id velit placerat molestie Donec dictum lectus non odio. Cras a ante vitae enim.</p></div>
</article>
<article class="abs book" style="left:609px">
  <div class="book-cover" role="img" aria-label="Photo of an open book" style="background:linear-gradient(180deg,#e8e2d6,#c9bda8 60%,#8a7a62)"></div>
  <div class="book-info"><h3>Book Title here</h3><div class="author">Author Name</div><p>Pellentesque faucibus Ut accumsan ultricies elit Maecenas at justo id velit placerat molestie Donec dictum lectus non odio. Cras a ante vitae enim.</p></div>
</article>

<div class="abs map" role="img" aria-label="Street map around the clinic location"></div>
<div class="abs contact-card">
  <h2>Contact Us</h2>
  <p>4820 Maple Ridge Road, Suite 210,<br>Fairview, OH 44126<br>(440) 555-0172<br>hello@serenovawellness.com</p>
</div>
<form class="abs form">
  <h2>Appointment Request</h2>
  <div class="field">First Name</div>
  <div class="field">Last Name</div>
  <div class="field">Email</div>
  <div class="field">Phone</div>
  <div class="check"><span class="box"></span><span>Please contact me for an appointment</span></div>
  <div class="submit">Submit</div>
</form>

<footer class="abs footer">
  <div><svg width="20" height="26" viewBox="0 0 20 26"><path d="M10 0a10 10 0 0 0-10 10c0 7 10 16 10 16s10-9 10-16A10 10 0 0 0 10 0Zm0 14a4 4 0 1 1 0-8 4 4 0 0 1 0 8Z" fill="#fff"/></svg>4820 Maple Ridge Road, Suite 210, Fairview, OH 44126</div>
  <div><svg width="22" height="22" viewBox="0 0 24 24"><path d="M6.6 10.8a15 15 0 0 0 6.6 6.6l2.2-2.2a1 1 0 0 1 1-.25 11.4 11.4 0 0 0 3.6.57 1 1 0 0 1 1 1V20a1 1 0 0 1-1 1A17 17 0 0 1 3 4a1 1 0 0 1 1-1h3.5a1 1 0 0 1 1 1c0 1.25.2 2.45.57 3.57a1 1 0 0 1-.25 1Z" fill="#fff"/></svg>(440) 555-0172</div>
  <div><svg width="24" height="18" viewBox="0 0 24 18"><rect width="24" height="18" rx="2" fill="#fff"/><path d="M1 2l11 8 11-8" fill="none" stroke="var(--blue-footer)" stroke-width="2"/></svg>hello@serenovawellness.com</div>
</footer>
<div class="abs copyright">© 2019 Company Name. All right reserved</div>

</body>
</html>
```